Pine Hollow Haven Home Inc. Website Update

We have a couple of broken links such as the "contact us" and would like to add board members and a calendar of events. We are open to a new design.

```html
<!DOCTYPE html>
<html lang="en">
<head>
<meta charset="utf-8">
<title>Pine Hollow Haven Home Inc.</title>
<link href="https://fonts.googleapis.com/css2?family=Cinzel:wght@400;700&family=Open+Sans:wght@400;600;700&display=swap" rel="stylesheet">
<style>
:root{
  --ink:#1b1b1b;
  --dark:#141414;
  --white:#ffffff;
  --grey:#6b6b6b;
  --light:#ececec;
  --line:#d4d4d4;
  --pink:#d8477f;
  --blue:#3b6fc2;
  --gold:#c99a2e;
}
*{box-sizing:border-box;margin:0;padding:0}
html,body{width:1200px;height:4839px;overflow:hidden;background:var(--white)}
body{font-family:"Open Sans",Arial,sans-serif;color:var(--ink)}
.page{position:relative;width:1200px;height:4839px;overflow:hidden}
.abs{position:absolute}
.serif{font-family:"Cinzel",Georgia,serif}

/* header */
.site-header{position:absolute;top:0;left:0;width:1200px;height:113px;background:var(--white);z-index:3}
.nav{position:absolute;top:48px;display:flex;gap:18px;font-size:15px;font-weight:700;text-transform:uppercase;letter-spacing:.3px}
.nav a{color:var(--ink);text-decoration:none}
.nav-left{left:162px}
.nav-right{left:690px}
.brand{position:absolute;left:480px;top:18px;width:240px;height:130px;background:var(--white);border-radius:0 0 120px 120px;display:flex;flex-direction:column;align-items:center;justify-content:center;gap:8px}
.brand-dot{width:34px;height:34px;border-radius:50%;background:var(--pink)}
.brand-name{font-family:"Open Sans",Arial,sans-serif;font-weight:700;font-size:15px;color:var(--pink);text-align:center;line-height:1.25;width:190px}

/* hero */
.hero{position:absolute;top:113px;left:0;width:1200px;height:661px;background:linear-gradient(120deg,#4a4440 0%,#7a6e66 35%,#55504c 65%,#2e2b29 100%)}
.hero-shade{position:absolute;inset:0;background:rgba(0,0,0,.35)}
.hero-kicker{position:absolute;top:155px;width:100%;text-align:center;color:var(--white);font-size:50px;letter-spacing:2px}
.hero-title{position:absolute;top:205px;width:100%;text-align:center;color:var(--white);font-size:56px;font-weight:700;letter-spacing:1px}
.hero-btns{position:absolute;top:292px;width:100%;display:flex;justify-content:center;gap:20px}
.btn-pill{height:54px;min-width:176px;padding:0 30px;border-radius:27px;display:inline-flex;align-items:center;justify-content:center;font-size:16px;font-weight:600;text-transform:uppercase;text-decoration:none}
.btn-outline{border:2px solid var(--white);color:var(--white)}
.btn-solid{background:#000;color:var(--white)}
.slider-arrow{position:absolute;top:238px;width:54px;height:54px;border-radius:50%;background:rgba(255,255,255,.55);display:flex;align-items:center;justify-content:center}

/* section heads */
.divider{position:absolute;left:570px;width:60px;height:4px;background:var(--ink);border-radius:2px}
.divider.light{background:var(--white)}
.section-title{position:absolute;width:100%;text-align:center;font-family:"Cinzel",Georgia,serif;font-weight:700;font-size:34px;line-height:1.15;color:var(--ink)}
.section-title.light{color:var(--white)}
.intro{position:absolute;top:900px;left:280px;width:640px;text-align:center;font-size:19px;line-height:1.55;color:#333}

/* services */
.service-card{position:absolute;width:261px;height:232px;border:2px solid var(--line);border-radius:14px;background:var(--white);box-shadow:0 6px 16px rgba(0,0,0,.08);text-align:center}
.service-icon{width:84px;height:84px;margin:28px auto 16px;border-radius:50%;border:3px solid #cfcfcf;display:flex;align-items:center;justify-content:center}
.service-name{font-family:"Cinzel",Georgia,serif;font-weight:700;font-size:16px;line-height:1.45;color:var(--ink);padding:0 28px}

/* video */
.video{position:absolute;left:306px;top:1365px;width:581px;height:371px;border:2px solid var(--line);border-radius:8px;background:var(--white);padding:14px}
.video-frame{width:100%;height:100%;background:linear-gradient(135deg,#cfc9c2 0%,#8e8680 45%,#5b5550 100%);display:flex;align-items:center;justify-content:center}
.play{width:80px;height:80px;border-radius:50%;background:var(--white);display:flex;align-items:center;justify-content:center}

/* events */
.calendar{position:absolute;left:161px;top:1978px;width:381px;height:364px;background:var(--white);border-radius:10px;padding:18px 22px}
.cal-head{height:44px;border-radius:22px;background:#5a5a5a;color:var(--white);display:flex;align-items:center;justify-content:space-between;padding:0 8px;font-family:"Cinzel",Georgia,serif;font-weight:700;font-size:20px}
.cal-nav{width:30px;height:30px;border-radius:50%;background:#777;display:flex;align-items:center;justify-content:center}
.cal-table{width:100%;border-collapse:collapse;margin-top:10px;font-size:17px;text-align:center}
.cal-table th{font-weight:700;height:38px;font-size:16px}
.cal-table td{height:41px;color:#333}
.event{position:absolute;left:574px;width:500px;height:115px;display:flex;gap:24px;color:var(--white)}
.event-thumb{width:112px;height:112px;border-radius:50%;flex:none}
.event-title{font-size:21px;font-weight:600;margin-top:6px}
.event-desc{font-size:14px;line-height:1.35;margin-top:4px;color:#e4e4e4;width:330px}
.event-more{font-size:13px;font-weight:700;margin-top:5px;text-transform:uppercase}

/* board */
.member{position:absolute;top:2620px;width:200px;text-align:center}
.member-photo{width:194px;height:194px;border-radius:50%;border:4px solid #dcdcdc;margin:0 auto}
.member-name{font-size:20px;font-weight:600;margin-top:24px}
.member-bio{font-size:13px;color:var(--grey);line-height:1.35;margin-top:6px;padding:0 18px}
.btn-small{display:inline-block;margin-top:22px;width:132px;height:40px;line-height:36px;border:2px solid #bbb;border-radius:20px;font-size:13px;font-weight:600;color:#444;text-transform:uppercase}

/* testimonial */
.quote{position:absolute;top:3218px;left:250px;width:700px;text-align:center;color:var(--white);font-size:21px;line-height:1.55}
.quote-mark{font-family:"Cinzel",Georgia,serif;font-size:72px;line-height:0;position:relative;top:22px}
.quote-name{position:absolute;top:3340px;width:100%;text-align:center;color:var(--white);font-size:22px;text-transform:uppercase;letter-spacing:1px}
.dots{position:absolute;top:3400px;left:575px;display:flex;gap:9px}
.dots span{width:12px;height:12px;border-radius:50%;border:2px solid var(--white)}
.dots span.on{background:var(--white)}

/* cta cards */
.cta{position:absolute;top:3587px;width:423px;height:284px;border-radius:40px 0 40px 0;text-align:center;padding-top:50px}
.cta-donate{left:168px;background:linear-gradient(135deg,#2a2a2a,#151515);color:var(--white)}
.cta-care{left:619px;background:linear-gradient(135deg,#e9e9e9,#d4d4d4);color:var(--ink)}
.cta-title{font-family:"Cinzel",Georgia,serif;font-weight:700;font-size:30px}
.cta-text{font-size:15px;line-height:1.45;margin:10px auto 0;width:330px}
.cta-btn{display:inline-block;margin-top:22px;width:160px;height:50px;line-height:46px;border:2px solid currentColor;border-radius:25px;font-size:15px;font-weight:600;text-transform:uppercase}
.cta-care .cta-btn{background:rgba(255,255,255,.7);border-color:#fff}

/* contact */
.contact-bg{position:absolute;top:3942px;left:0;width:1200px;height:510px;background:linear-gradient(180deg,#f4f4f4,#e2e2e2)}
.field{position:absolute;height:51px;background:var(--white);border:1px solid #ddd;font-size:16px;color:#555;padding:14px 16px}
.submit{position:absolute;left:518px;top:4316px;width:170px;height:49px;border-radius:25px;background:#000;color:var(--white);font-size:18px;font-weight:600;display:flex;align-items:center;justify-content:center}

/* footer */
.site-footer{position:absolute;top:4452px;left:0;width:1200px;height:387px;background:#000;color:var(--white)}
.foot-brand{position:absolute;left:150px;top:80px;width:200px;display:flex;flex-direction:column;align-items:center;gap:12px}
.foot-brand .brand-dot{width:50px;height:50px}
.foot-head{position:absolute;top:60px;font-family:"Cinzel",Georgia,serif;font-weight:700;font-size:17px;letter-spacing:.5px}
.foot-list{position:absolute;top:103px;list-style:none;font-size:15px;line-height:1.45}
.foot-contact li{display:flex;gap:10px;align-items:flex-start;margin-bottom:16px}
.social{position:absolute;left:904px;top:104px;display:flex;gap:10px}
.social span{width:28px;height:28px;border-radius:50%;background:var(--blue)}
.badge{position:absolute;left:914px;top:150px;width:92px;height:92px;border-radius:50%;background:radial-gradient(circle,#e8c45a,var(--gold) 70%,#8a6418)}
.foot-rule{position:absolute;top:310px;left:0;width:1200px;height:1px;background:#333}
.copyright{position:absolute;top:338px;width:100%;text-align:center;font-size:14px;color:#ccc}
</style>
</head>
<body>
<div class="page">

  <header class="site-header">
    <nav class="nav nav-left"><a>About</a><a>How you can help</a><a>Services</a></nav>
    <div class="brand"><span class="brand-dot"></span><span class="brand-name">Pine Hollow Haven Home Inc.</span></div>
    <nav class="nav nav-right"><a>Our love of pets</a><a>Contact us</a><a>Haven Walk</a></nav>
  </header>

  <section class="hero" role="img" aria-label="Photo of three young women studying together on the floor">
    <div class="hero-shade"></div>
    <div class="slider-arrow" style="left:78px"><svg width="18" height="18" viewBox="0 0 18 18"><path d="M12 2 5 9l7 7" fill="none" stroke="#222" stroke-width="2.5"/></svg></div>
    <div class="slider-arrow" style="left:1026px"><svg width="18" height="18" viewBox="0 0 18 18"><path d="M6 2l7 7-7 7" fill="none" stroke="#222" stroke-width="2.5"/></svg></div>
    <div class="hero-kicker serif">WELCOME TO</div>
    <h1 class="hero-title serif">PINE HOLLOW HAVEN HOME INC.</h1>
    <div class="hero-btns"><a class="btn-pill btn-outline">Our Mission</a><a class="btn-pill btn-solid">Our Girls</a></div>
    <svg class="abs" style="left:0;bottom:0" width="1200" height="140" viewBox="0 0 1200 140" preserveAspectRatio="none">
      <path d="M0 80 Q600 -20 1200 90 L1200 140 L0 140Z" fill="#000"/>
      <path d="M0 100 Q600 5 1200 110 L1200 140 L0 140Z" fill="#fff"/>
    </svg>
  </section>

  <div class="divider" style="top:790px"></div>
  <h2 class="section-title" style="top:818px">WE ARE PINE HOLLOW<br>HAVEN HOME</h2>
  <p class="intro">With the help of our community, we have raised over 1000 girls and counting! Some of the services we offer include:</p>

  <div class="service-card" style="left:181px;top:1010px">
    <div class="service-icon"><svg width="44" height="44" viewBox="0 0 44 44"><rect x="6" y="10" width="32" height="22" rx="2" fill="none" stroke="#333" stroke-width="3"/><path d="M6 22h32M6 32v6M38 32v6" stroke="#333" stroke-width="3"/></svg></div>
    <div class="service-name">ROOM, BOARD, AND WATCHFUL OVERSIGHT</div>
  </div>
  <div class="service-card" style="left:465px;top:1048px">
    <div class="service-icon"><svg width="44" height="44" viewBox="0 0 44 44"><path d="M22 37 7 22a8 8 0 0 1 15-10 8 8 0 0 1 15 10Z" fill="none" stroke="#333" stroke-width="3"/></svg></div>
    <div class="service-name">TRANSITIONAL LIVING SERVICES</div>
  </div>
  <div class="service-card" style="left:752px;top:1010px">
    <div class="service-icon"><svg width="44" height="44" viewBox="0 0 44 44"><path d="M14 38V16M20 38V10M26 38V12M32 38V18M12 38h22" stroke="#333" stroke-width="3" stroke-linecap="round"/></svg></div>
    <div class="service-name">INDEPENDENT LIVING SERVICES</div>
  </div>

  <div class="video">
    <div class="video-frame" role="img" aria-label="Video still of a bright living room with a fireplace">
      <div class="play"><svg width="30" height="30" viewBox="0 0 30 30"><path d="M9 5l16 10-16 10Z" fill="#111"/></svg></div>
    </div>
  </div>

  <section class="events">
    <svg class="abs" style="left:0;top:1790px" width="1200" height="650" viewBox="0 0 1200 650" preserveAspectRatio="none">
      <path d="M0 40 Q700 -10 1200 10 L1200 560 Q700 520 0 640Z" fill="#c9c9c9"/>
      <path d="M0 40 Q700 30 1200 60 L1200 540 Q700 560 0 620Z" fill="var(--dark)"/>
    </svg>
    <div class="divider light" style="top:1865px"></div>
    <h2 class="section-title light" style="top:1885px">EVENT CALENDAR</h2>

    <div class="calendar">
      <div class="cal-head">
        <span class="cal-nav"><svg width="12" height="12" viewBox="0 0 12 12"><path d="M8 1 3 6l5 5" fill="none" stroke="#fff" stroke-width="2"/></svg></span>
        MARCH 2019
        <span class="cal-nav"><svg width="12" height="12" viewBox="0 0 12 12"><path d="M4 1l5 5-5 5" fill="none" stroke="#fff" stroke-width="2"/></svg></span>
      </div>
      <table class="cal-table">
        <tr><th>MO</th><th>TU</th><th>WE</th><th>TH</th><th>FR</th><th>SA</th><th>SU</th></tr>
        <tr><td></td><td></td><td></td><td></td><td>1</td><td>2</td><td>3</td></tr>
        <tr><td>4</td><td>5</td><td>6</td><td>7</td><td>8</td><td>9</td><td>10</td></tr>
        <tr><td>11</td><td>12</td><td>13</td><td>14</td><td>15</td><td>16</td><td>17</td></tr>
        <tr><td>18</td><td>19</td><td>20</td><td>21</td><td>22</td><td>23</td><td>24</td></tr>
        <tr><td>25</td><td>26</td><td>27</td><td>28</td><td>29</td><td>30</td><td>31</td></tr>
      </table>
    </div>

    <div class="event" style="top:1978px">
      <div class="event-thumb" role="img" aria-label="Event photo" style="background:linear-gradient(135deg,#6a3aa8,#2b1550)"></div>
      <div><div class="event-title">Event Title here</div><div class="event-desc">Join us for an afternoon of fellowship, food and fun with our girls.</div><div class="event-more">Read more</div></div>
    </div>
    <div class="event" style="top:2113px">
      <div class="event-thumb" role="img" aria-label="Event photo" style="background:linear-gradient(135deg,#c9a98c,#6e5646)"></div>
      <div><div class="event-title">Event Title here</div><div class="event-desc">Join us for an afternoon of fellowship, food and fun with our girls.</div><div class="event-more">Read more</div></div>
    </div>
    <div class="event" style="top:2248px">
      <div class="event-thumb" role="img" aria-label="Event photo" style="background:linear-gradient(135deg,#8fb3c9,#3f5a6b)"></div>
      <div><div class="event-title">Event Title here</div><div class="event-desc">Join us for an afternoon of fellowship, food and fun with our girls.</div><div class="event-more">Read more</div></div>
    </div>
  </section>

  <section class="board">
    <div class="divider" style="top:2505px;background:#bbb"></div>
    <h2 class="section-title" style="top:2545px">BOARD MEMBERS</h2>
    <div class="member" style="left:161px"><div class="member-photo" role="img" aria-label="Portrait of a board member" style="background:linear-gradient(135deg,#d8b9a0,#8c6a55)"></div><div class="member-name">Member Name</div><div class="member-bio">Serving our community with care and heart.</div><span class="btn-small">Read more</span></div>
    <div class="member" style="left:384px"><div class="member-photo" role="img" aria-label="Portrait of a board member" style="background:linear-gradient(135deg,#e6d2b4,#9a8466)"></div><div class="member-name">Member Name</div><div class="member-bio">Serving our community with care and heart.</div><span class="btn-small">Read more</span></div>
    <div class="member" style="left:623px"><div class="member-photo" role="img" aria-label="Portrait of a board member" style="background:linear-gradient(135deg,#cdd8e6,#5d7394)"></div><div class="member-name">Member Name</div><div class="member-bio">Serving our community with care and heart.</div><span class="btn-small">Read more</span></div>
    <div class="member" style="left:836px"><div class="member-photo" role="img" aria-label="Portrait of a board member" style="background:linear-gradient(135deg,#eee7df,#a6958a)"></div><div class="member-name">Member Name</div><div class="member-bio">Serving our community with care and heart.</div><span class="btn-small">Read more</span></div>
  </section>

  <section class="testimonials">
    <svg class="abs" style="left:0;top:3020px" width="1200" height="500" viewBox="0 0 1200 500" preserveAspectRatio="none" role="img" aria-label="Dark photo of a young woman at a desk">
      <defs><linearGradient id="tg" x1="0" y1="0" x2="1" y2="1"><stop offset="0" stop-color="#2c2c2c"/><stop offset="1" stop-color="#111"/></linearGradient></defs>
      <path d="M0 10 Q600 60 1200 40 L1200 460 Q600 430 0 500Z" fill="#bdbdbd"/>
      <path d="M0 10 Q600 40 1200 60 L1200 440 Q600 450 0 480Z" fill="url(#tg)"/>
    </svg>
    <div class="divider light" style="top:3118px"></div>
    <h2 class="section-title light" style="top:3150px">WHAT OUR GIRLS SAY</h2>
    <p class="quote"><span class="quote-mark">&ldquo;</span> Emotionally healed a lot and I felt supported. &nbsp;I learned how to cook, budget, get a job, buy a car, pay bills, community service and helping others. &nbsp;I would not have gotten here without the Haven Home. <span class="quote-mark">&rdquo;</span></p>
    <div class="quote-name">Marisol</div>
    <div class="dots"><span></span><span class="on"></span><span></span></div>
  </section>

  <div class="cta cta-donate" role="img" aria-label="Donate panel over a dark photo">
    <div class="cta-title">DONATE</div>
    <p class="cta-text">We appreciate donations from our community! It is because of the hearts of those around us that we're able to do what we do.</p>
    <span class="cta-btn">Donate now</span>
  </div>
  <div class="cta cta-care" style="border-radius:0 40px 0 40px">
    <div class="cta-title">CARE</div>
    <p class="cta-text">Council for Residential Care Standards certified since 2009<br>To learn more about our CRCS accreditation, please visit www.crcs-example.org</p>
    <span class="cta-btn">Click here</span>
  </div>

  <section class="contact">
    <div class="contact-bg" role="img" aria-label="Faded photo of hands writing"></div>
    <svg class="abs" style="left:0;top:3930px" width="1200" height="80" viewBox="0 0 1200 80" preserveAspectRatio="none">
      <path d="M0 0 H1200 V20 Q600 -10 0 70Z" fill="#fff"/>
      <path d="M0 70 Q600 -10 1200 20" fill="none" stroke="#111" stroke-width="4"/>
    </svg>
    <div class="divider" style="top:3995px"></div>
    <h2 class="section-title" style="top:4020px;font-size:32px">CONTACT US</h2>
    <div class="field" style="left:194px;top:4081px;width:403px">Your Name</div>
    <div class="field" style="left:610px;top:4081px;width:406px">Phone</div>
    <div class="field" style="left:194px;top:4141px;width:403px">Email</div>
    <div class="field" style="left:610px;top:4141px;width:406px">City</div>
    <div class="field" style="left:194px;top:4204px;width:822px;height:88px">Message</div>
    <div class="submit">Submit</div>
  </section>

  <footer class="site-footer">
    <div class="foot-brand"><span class="brand-dot"></span><span class="brand-name">Pine Hollow Haven Home Inc.</span></div>

    <div class="foot-head" style="left:446px">CONTACT US</div>
    <ul class="foot-list foot-contact" style="left:450px;width:240px">
      <li><svg width="16" height="20" viewBox="0 0 16 20"><path d="M8 19S2 11 2 7a6 6 0 0 1 12 0c0 4-6 12-6 12Z" fill="#fff"/><circle cx="8" cy="7" r="2.2" fill="#000"/></svg><span>418 Birchwood Ln, Maple Ridge, GA 30999, USA</span></li>
      <li><svg width="16" height="18" viewBox="0 0 16 18"><path d="M3 1h3l2 4-2 2a9 9 0 0 0 4 4l2-2 4 2v3c0 1-1 2-2 2C7 16 1 10 1 3c0-1 1-2 2-2Z" fill="#fff"/></svg><span>555.014.2288</span></li>
      <li><svg width="16" height="14" viewBox="0 0 16 14"><rect x="1" y="2" width="14" height="10" fill="none" stroke="#fff" stroke-width="1.6"/><path d="M1 2l7 6 7-6" fill="none" stroke="#fff" stroke-width="1.6"/></svg><span>hello@pinehollowhaven.org</span></li>
    </ul>

    <div class="foot-head" style="left:715px">COMPANY</div>
    <ul class="foot-list" style="left:718px">
      <li>About us</li><li>Haven Walk</li><li>Services</li><li>How you can help</li><li>Our Love of Pets</li>
    </ul>

    <div class="foot-head" style="left:904px">GET IN TOUCH</div>
    <div class="social"><span></span><span></span><span></span><span></span></div>
    <div class="badge"></div>

    <div class="foot-rule"></div>
    <p class="copyright">Copyright &copy; 2019 All right reserved</p>
  </footer>

</div>
</body>
</html>
```